Business Card Design For Marketing Agnecy LVP

Need business card design for marketing agency.

Doug Fenwick
President, CEO
1-555-302-4196
doug@boldpromoperksgroup.example
www.BoldPromoPerksGroup.example

Back Side:
Boost Sales Using Rewards, Incentives & Giveaways
Get A Free Sample Package

Target Market(s)

B2B

Industry/Entity Type

Marketing

Contact Information for Business Card

Doug Fenwick
President, CEO
1-555-302-4196

Back Side:
Get A Free Sample Package

Please note that my current url is OLD DESIGN. I am working on new design and want the business card to match color themes at least on new site. Here is the demo link for new site so you can see the colors I use, etc.

http://layoutcratehub.example/kq/doug/lvp_final/index.html

Requirements
Must have
• Please note that my current url is OLD DESIGN. I am working on new design and want the business card to match color themes at least on new site. Here is the demo link for new site so you can see the colors I use, etc.

Nice to have

Should not have

```html
<!DOCTYPE html>
<html lang="en">
<head>
<meta charset="utf-8">
<title>Bold Promo Perks Group Business Card</title>
<link rel="stylesheet" href="https://fonts.googleapis.com/css2?family=Montserrat:wght@600;800&family=Roboto:wght@400&display=swap">
<style>
  :root {
    --brand-blue: #1a72c2;
    --ink-grey: #4a4a4a;
    --rule-grey: #b9b9b9;
    --paper: #ffffff;
    --table: #2c2c2c;
  }
  * { box-sizing: border-box; margin: 0; padding: 0; }
  html, body { width: 1200px; height: 866px; overflow: hidden; }
  body {
    background: var(--table);
    display: flex;
    flex-direction: column;
    align-items: center;
    justify-content: center;
    gap: 30px;
    font-family: "Roboto", Arial, sans-serif;
  }
  .card {
    width: 680px;
    height: 388px;
    position: relative;
    overflow: hidden;
    box-shadow: 0 10px 24px rgba(0,0,0,.45);
  }

  /* Front */
  .card-front { background: var(--paper); }
  .card-front::after {
    content: ""; position: absolute; left: 0; right: 0; bottom: 0;
    height: 12px; background: var(--brand-blue);
  }
  .contact-block { position: absolute; left: 44px; top: 70px; }
  .person-name {
    font-family: "Montserrat", Arial, sans-serif;
    font-weight: 800; font-size: 25px; letter-spacing: .5px;
    color: var(--brand-blue); text-transform: uppercase;
  }
  .person-title { font-size: 17px; color: var(--ink-grey); margin-top: 2px; }
  .contact-list { list-style: none; margin-top: 22px; }
  .contact-list li {
    display: flex; align-items: center; gap: 9px;
    font-size: 16px; color: var(--ink-grey); line-height: 25px;
  }
  .contact-list svg { width: 14px; height: 14px; fill: var(--ink-grey); flex: none; }
  .contact-list .web-link { color: var(--brand-blue); }

  .brand-wordmark {
    position: absolute; right: 44px; top: 248px;
    font-family: "Montserrat", Arial, sans-serif;
    font-weight: 800; font-size: 38px; line-height: 1.08;
    color: var(--brand-blue); text-transform: uppercase;
    text-align: right; letter-spacing: 1px; white-space: nowrap;
  }
  .brand-rule {
    position: absolute; left: 270px; right: 44px; bottom: 36px;
    height: 1px; background: var(--rule-grey);
  }

  /* Back */
  .card-back {
    background: var(--brand-blue);
    display: flex; flex-direction: column; align-items: center; justify-content: center;
    color: var(--paper); text-align: center;
  }
  .back-name {
    font-family: "Montserrat", Arial, sans-serif;
    font-weight: 800; font-size: 52px; line-height: 1.05; text-transform: uppercase;
    letter-spacing: 1px;
  }
  .back-rule { width: 470px; height: 2px; background: var(--paper); margin: 14px 0 22px; opacity: .9; }
  .tagline {
    font-family: "Montserrat", Arial, sans-serif;
    font-weight: 600; font-size: 17px; line-height: 1.35; text-transform: uppercase;
  }
  .back-url { font-size: 16px; margin-top: 22px; padding-top: 8px; border-top: 1px solid rgba(255,255,255,.35); }
</style>
</head>
<body>

  <section class="card card-front" aria-label="Business card front">
    <div class="contact-block">
      <h1 class="person-name">Doug Fenwick</h1>
      <p class="person-title">President, CEO</p>
      <ul class="contact-list">
        <li>
          <svg viewBox="0 0 24 24" aria-hidden="true"><path d="M6.6 10.8a15 15 0 0 0 6.6 6.6l2.2-2.2a1 1 0 0 1 1-.25 11.4 11.4 0 0 0 3.6.57 1 1 0 0 1 1 1V20a1 1 0 0 1-1 1A17 17 0 0 1 3 4a1 1 0 0 1 1-1h3.5a1 1 0 0 1 1 1c0 1.25.2 2.450.57 3.57a1 1 0 0 1-.25 1z"/></svg>
          1-555-302-4196
        </li>
        <li>
          <svg viewBox="0 0 24 24" aria-hidden="true"><path d="M2 5h20v14H2zm2 2v.5l8 5 8-5V7l-8 5z"/></svg>
          doug@boldpromoperksgroup.example
        </li>
        <li>
          <svg viewBox="0 0 24 24" aria-hidden="true"><circle cx="12" cy="12" r="10"/></svg>
          <span class="web-link">www.BoldPromoPerksGroup.example</span>
        </li>
      </ul>
    </div>

    <p class="brand-wordmark">Bold Promo<br>Perks Group</p>
    <div class="brand-rule" aria-hidden="true"></div>
  </section>

  <section class="card card-back" aria-label="Business card back">
    <h2 class="back-name">Bold Promo<br>Perks Group</h2>
    <div class="back-rule" aria-hidden="true"></div>
    <p class="tagline">Boost sales using rewards<br>incentives &amp; giveaways<br>Get a free sample package</p>
    <p class="back-url">www.BoldPromoPerksGroup.example</p>
  </section>

</body>
</html>
```